Window and GutterCleaning Flyer A5 size double sided.

We need a double sided A5 flyer. Side 1, is for window cleaning, side 2 is for gutter cleaning. Licensed by Borough of Marlow Council.
Phone number 0800 473 1926.
Business address 17 Fallowmere Close, North Brack Edinburgh EH31 4LP.
www.clearpane-hub-services.com
We use a LoftEye Gutter inspection Cam to view your gutters first to see if they need doing.
Window cleaning ; Professional window cleaning services, what we offer, water fed pole window cleaning able to reach windows up to 60 feet.
Conservatory cleaning.
Conservatory roof cleaning.
Fascias & Soffits cleaning.
Excellent Customer Service.
Target Market(s)
domestic houses
Industry/Entity Type
window cleaning
Look and feel
Each slider illustrates characteristics of the customer's brand and the style your logo design should communicate.

```html
<!DOCTYPE html>
<html lang="en">
<head>
<meta charset="utf-8">
<title>ClearPane Hub – Window &amp; Gutter Cleaning Flyer</title>
<link rel="stylesheet" href="https://fonts.googleapis.com/css2?family=Anton&family=Jost:wght@400;500&family=Poppins:wght@600;700;800;900&display=swap">
<style>
  :root{
    --sky:#3cb5fb;
    --navy:#2e2660;
    --ink:#2a2a2a;
    --charcoal:#2c2c2c;
    --deep:#0f3f73;
    --light-blue:#a9d2f2;
    --accent:#3ab6f3;
    --white:#ffffff;
    --badge:#d9b45a;
  }
  *{box-sizing:border-box;margin:0;padding:0}
  html,body{width:1200px;height:773px;overflow:hidden;background:var(--sky)}
  .canvas{position:relative;width:1200px;height:773px;background:var(--sky);font-family:"Poppins",sans-serif}

  .side{position:absolute;top:18px;width:569px;height:737px;overflow:hidden}
  .side--windows{left:20px;background:var(--white)}
  .side--gutters{left:611px;background:var(--deep)}

  .art{position:absolute;left:0;top:0}

  .brand{position:absolute;display:flex;align-items:center;gap:8px;color:var(--navy);
    font-family:"Poppins",sans-serif;font-weight:800;font-size:21px;line-height:1.1}
  .brand__mark{width:14px;height:14px;background:var(--navy);flex:none}
  .side--windows .brand{left:40px;top:190px;width:160px}
  .side--gutters .brand{left:30px;top:110px;width:160px;background:var(--light-blue);padding:10px 10px}

  .headline{position:absolute;left:36px;top:296px;font-weight:900;font-size:51px;color:var(--navy);letter-spacing:-.5px;line-height:1}
  .subhead{position:absolute;left:35px;top:350px;font-weight:800;font-size:29.5px;color:var(--ink);line-height:1}
  .reach{position:absolute;left:39px;top:397px;font-weight:800;font-size:12.4px;color:var(--ink)}
  .intro{position:absolute;left:39px;top:421px;width:510px;font-family:"Jost",sans-serif;font-size:14.2px;line-height:18.3px;color:var(--ink)}

  .offer-tab{position:absolute;left:0;top:514px;width:248px;height:36px;background:var(--charcoal);
    border-radius:0 18px 18px 0;color:var(--white);font-weight:700;font-size:18px;line-height:36px;padding-left:39px}
  .offers{position:absolute;left:39px;top:565px;width:495px;display:grid;grid-template-columns:242px 242px;gap:10px 10px;list-style:none}
  .offers li{height:37px;border-radius:19px;background:var(--navy);color:var(--white);
    font-family:"Jost",sans-serif;font-size:15.5px;line-height:37px;padding-left:14px}
  .offers li::before{content:"•";margin-right:12px;font-size:16px}

  .licence{position:absolute;left:0;top:668px;width:569px;text-align:center;font-weight:800;font-size:20.5px;line-height:22px;color:var(--ink)}

  .gutter-title{position:absolute;left:33px;top:428px;font-family:"Anton",sans-serif;font-size:67px;color:var(--white);line-height:1;letter-spacing:-1px}
  .gutter-sub{position:absolute;left:34px;top:498px;font-weight:800;font-size:22px;color:var(--accent);line-height:1}
  .gutter-copy{position:absolute;right:28px;top:430px;width:280px;text-align:right;font-family:"Jost",sans-serif;font-size:12px;line-height:15.4px;color:var(--white)}
  .cam-note{position:absolute;left:0;top:528px;width:569px;text-align:center;font-weight:800;font-size:12.4px;line-height:13.5px;color:var(--white)}

  .why{position:absolute;left:27px;top:567px;width:513px;height:77px;background:var(--white);border-radius:22px;display:flex;align-items:center}
  .why__label{width:120px;height:100%;border-right:2px solid var(--navy);display:flex;align-items:center;padding-left:19px;
    font-weight:800;font-size:14.5px;line-height:13px;color:var(--navy)}
  .why__list{list-style:none;display:grid;grid-template-columns:206px 180px;gap:8px 0;padding-left:16px;font-weight:700;font-size:11.3px;color:var(--ink)}
  .why__list li::before{content:"•";margin-right:8px}

  .contacts{position:absolute;left:0;top:668px;width:569px;height:69px}
  .contact{position:absolute;top:0;height:69px;font-weight:700;font-size:9.6px;color:var(--ink)}
  .contact__icon{position:absolute;top:5px;left:50%;margin-left:-10px;width:20px;height:20px}
  .contact__text{position:absolute;left:0;right:0;bottom:14px;text-align:center;white-space:nowrap}
  .contact--address{left:0;width:176px;background:var(--white);font-size:8.8px}
  .contact--address .contact__text{left:16px;text-align:left;line-height:12px;bottom:12px}
  .contact--web{left:186px;width:196px;background:var(--sky);font-size:9.8px}
  .contact--phone{left:392px;width:177px;background:var(--white);font-size:11px}
</style>
</head>
<body>
<div class="canvas">

  <section class="side side--windows" aria-label="Window cleaning side">
    <svg class="art" width="569" height="737" viewBox="0 0 569 737">
      <defs>
        <linearGradient id="houseTone" x1="0" y1="0" x2="1" y2="1">
          <stop offset="0" stop-color="#8f7466"/><stop offset=".5" stop-color="#a8857a"/><stop offset="1" stop-color="#6e6a5a"/>
        </linearGradient>
        <linearGradient id="glassTone" x1="0" y1="0" x2="1" y2="1">
          <stop offset="0" stop-color="#b9cfe0"/><stop offset=".5" stop-color="#9a6e5c"/><stop offset="1" stop-color="#cfd9e2"/>
        </linearGradient>
      </defs>
      <rect x="0" y="0" width="569" height="737" fill="#fff"/>
      <path role="img" aria-label="Photo of a brick semi-detached house with clean windows" d="M60 0 H569 V350 C520 320 470 300 430 300 C360 210 260 80 100 50 C80 45 70 30 60 0 Z" fill="url(#houseTone)"/>
      <path d="M0 0 H85 C75 60 45 95 0 98 Z" fill="var(--navy)"/>
      <polygon role="img" aria-label="Photo of a window being cleaned with a water fed pole" points="280,44 400,44 455,154 400,268 280,268 200,154" fill="url(#glassTone)" stroke="#fff" stroke-width="6"/>
      <circle cx="480" cy="283" r="56" fill="var(--badge)"/>
    </svg>

    <div class="brand"><span class="brand__mark"></span><span>ClearPane Hub</span></div>

    <h1 class="headline">PROFESSIONAL</h1>
    <h2 class="subhead">WINDOW CLEANING SERVICES</h2>
    <p class="reach">WATER FED POLE WINDOW CLEANING ABLE TO REACH WINDOWS UP TO 60 FEET.</p>
    <p class="intro">We offer a high-quality, professional window cleaning service across West Edinburgh. Regular domestic or commercial window cleaning helps to avoid the build-up of dirt and residue on the glass, meaning more light can get into your home or business. It can also improve the external appearance of your property.</p>

    <div class="offer-tab">We Also Offer:</div>
    <ul class="offers">
      <li>Conservatory Cleaning</li>
      <li>Conservatory Roof Cleaning</li>
      <li>Fascias &amp; Soffits Cleaning</li>
      <li>Excellent Customer Service</li>
    </ul>

    <p class="licence">LICENSED AND REGULATED BY BOROUGH OF<br>MARLOW COUNCIL</p>
  </section>

  <section class="side side--gutters" aria-label="Gutter cleaning side">
    <svg class="art" width="569" height="737" viewBox="0 0 569 737">
      <defs>
        <linearGradient id="deepTone" x1="0" y1="0" x2="0" y2="1">
          <stop offset="0" stop-color="#1c67a8"/><stop offset="1" stop-color="#0d335f"/>
        </linearGradient>
        <linearGradient id="gutterTone" x1="0" y1="0" x2="1" y2="1">
          <stop offset="0" stop-color="#8e8e88"/><stop offset=".45" stop-color="#d9dad6"/><stop offset=".8" stop-color="#3b4fb0"/><stop offset="1" stop-color="#7a4a3e"/>
        </linearGradient>
        <linearGradient id="roofTone" x1="0" y1="0" x2="1" y2="1">
          <stop offset="0" stop-color="#8a7a60"/><stop offset="1" stop-color="#b9bcbf"/>
        </linearGradient>
        <linearGradient id="conservTone" x1="0" y1="0" x2="0" y2="1">
          <stop offset="0" stop-color="#9fc7e6"/><stop offset="1" stop-color="#a86a4c"/>
        </linearGradient>
        <linearGradient id="vacTone" x1="0" y1="0" x2="1" y2="1">
          <stop offset="0" stop-color="#6f9a55"/><stop offset="1" stop-color="#4a4f57"/>
        </linearGradient>
      </defs>
      <rect width="569" height="737" fill="url(#deepTone)"/>
      <path role="img" aria-label="Photo of a vacuum hose clearing moss from a gutter" d="M0 0 H569 V180 C470 280 360 250 250 300 C180 330 80 345 0 350 Z" fill="url(#gutterTone)"/>
      <path d="M0 350 C80 345 180 330 250 300 C360 250 470 280 569 180 V215 C470 300 360 290 250 330 C170 360 80 378 0 382 Z" fill="var(--white)"/>
      <path d="M0 382 C80 378 170 360 250 330 C360 290 470 300 569 215 V230 C480 330 360 330 250 360 C170 385 80 398 0 400 Z" fill="var(--sky)"/>
      <circle cx="397" cy="270" r="107" fill="#fff"/>
      <circle role="img" aria-label="Photo of a mossy conservatory roof" cx="397" cy="270" r="94" fill="url(#roofTone)"/>
      <circle cx="262" cy="312" r="80" fill="#fff"/>
      <circle role="img" aria-label="Photo of a clean white conservatory" cx="262" cy="312" r="71" fill="url(#conservTone)"/>
      <circle cx="139" cy="338" r="70" fill="#fff"/>
      <circle role="img" aria-label="Photo of a gutter vacuum pole at work" cx="139" cy="338" r="62" fill="url(#vacTone)"/>
    </svg>

    <div class="brand"><span class="brand__mark"></span><span>ClearPane Hub</span></div>

    <h2 class="gutter-title">GUTTER</h2>
    <p class="gutter-sub">CLEANING SERVICE</p>
    <p class="gutter-copy">If your gutters are blocked and overflowing, why not contact us for a free no obligation quote to clear them out and get them working as they should. With our gutter cleaning service we will clear all gutters and unblock all downpipes ensuring the water is running freely and down your drains.</p>
    <p class="cam-note">WE USE A LOFTEYE GUTTER INSPECTION CAM TO VIEW YOUR GUTTERS<br>FIRST TO SEE IF THEY NEED DOING.</p>

    <div class="why">
      <div class="why__label">Why<br>Choose Us?</div>
      <ul class="why__list">
        <li>Friendly, professional service</li>
        <li>Fully licensed and insured</li>
        <li>Excellent customer satisfaction</li>
        <li>Reliable and efficient</li>
      </ul>
    </div>

    <div class="contacts">
      <div class="contact contact--address">
        <svg class="contact__icon" width="20" height="20" viewBox="0 0 24 24" aria-hidden="true"><circle cx="12" cy="12" r="11" fill="var(--navy)"/><path d="M12 5a4.5 4.5 0 0 0-4.5 4.5C7.5 13 12 18 12 18s4.5-5 4.5-8.5A4.5 4.5 0 0 0 12 5z" fill="#fff"/><circle cx="12" cy="9.5" r="1.7" fill="var(--navy)"/></svg>
        <span class="contact__text">17 Fallowmere Close, North Brack<br>Edinburgh EH31 4LP</span>
      </div>
      <div class="contact contact--web">
        <svg class="contact__icon" width="20" height="20" viewBox="0 0 24 24" aria-hidden="true"><circle cx="12" cy="12" r="11" fill="var(--navy)"/><g fill="none" stroke="#fff" stroke-width="1.2"><circle cx="12" cy="12" r="6.5"/><ellipse cx="12" cy="12" rx="3" ry="6.5"/><path d="M5.5 12h13M6.5 9h11M6.5 15h11"/></g></svg>
        <span class="contact__text">www.clearpane-hub-services.com</span>
      </div>
      <div class="contact contact--phone">
        <svg class="contact__icon" width="20" height="20" viewBox="0 0 24 24" aria-hidden="true"><circle cx="12" cy="12" r="11" fill="var(--navy)"/><path d="M8.5 6.5l2 .2 1 2.6-1.4 1.1a7 7 0 0 0 3.5 3.5l1.1-1.4 2.6 1 .2 2c-.3.9-1.2 1.5-2.2 1.4A10 10 0 0 1 7.1 8.7c-.1-1 .5-1.9 1.4-2.2z" fill="#fff"/></svg>
        <span class="contact__text">0800 473 1926</span>
      </div>
    </div>
  </section>

</div>
</body>
</html>
```